11X17 Poster Trim A Frock Notch Quest

We are having a 21-Day Trim A Frock Notch Quest for our Fitness Studio. We need a poster designed using the template attached as a reference. I have included our Vorelump Bootcamps logo to put in the poster as well. Please DO NOT use the graphics in the flyer as we are expecting something much better :)
- Size needed 11x17 with bleeding for printing
- We need this made in Photoshop (CS3 friendly) or at least delivered in PS as we might change some text or re-arrange the design later on.

Target Market(s)

Personal Training Studio

Industry/Entity Type

Printing

Colors
0255a3
3377b5
85acd3
f37123
f68e4e
faa54b
f78f20
0692cd
34a7d8

Requirements
Must have
• Must be 11x17 with bleed for printing
• Must be in PS file (CS3 compatible)
• Must include our Vorelump Bootcamps logo somewhere in the poster
• Must include the information provided in the attached flyer
Nice to have
• Nice to have quality graphics that coincide with the challenge and our logo
Should not have
• Please NO scantily dressed women :)

```html
<!DOCTYPE html>
<html lang="en">
<head>
<meta charset="utf-8">
<title>Trim A Frock Notch Quest Poster</title>
<link href="https://fonts.googleapis.com/css2?family=Roboto+Condensed:ital,wght@0,300;0,400;0,700;0,800;1,400;1,800&display=swap" rel="stylesheet">
<style>
  :root {
    --ink: #2a2a2a;
    --black: #1c1c1c;
    --blue: #3377b5;
    --blue-deep: #0255a3;
    --paper: #ffffff;
    --paper-edge: #e2e2e2;
    --stage: #f2f2f2;
  }
  * { margin: 0; padding: 0; box-sizing: border-box; }
  html, body { width: 1200px; height: 1000px; overflow: hidden; }
  body {
    background: var(--stage);
    font-family: "Roboto Condensed", "Arial Narrow", sans-serif;
    color: var(--ink);
    position: relative;
  }
  .poster {
    position: absolute;
    left: 287px; top: 14px;
    width: 626px; height: 963px;
    background: radial-gradient(ellipse at 50% 45%, var(--paper) 55%, var(--paper-edge) 100%);
    overflow: hidden;
  }
  .poster > * { position: absolute; }
  .hero-photo {
    left: 50px; top: 5px; width: 275px; height: 510px;
    border-radius: 120px 120px 30px 30px;
    background: radial-gradient(ellipse at 45% 25%, #d9b49a 0 18%, transparent 32%),
                linear-gradient(180deg, #efe6df 0%, #8fd3e3 45%, #5fc0d6 80%, rgba(255,255,255,0) 100%);
    opacity: .9;
  }
  .brand {
    left: 279px; top: 70px; width: 250px; height: 60px;
    display: flex; align-items: center; gap: 10px;
    font-weight: 800; font-size: 24px; letter-spacing: .3px;
    text-transform: uppercase; color: var(--black); line-height: 1; white-space: nowrap;
  }
  .brand-mark { width: 16px; height: 16px; background: var(--black); flex: none; }

  .headline-group { left: 0; top: 0; width: 100%; height: 100%; pointer-events: none; }
  .headline {
    position: absolute; display: block;
    color: var(--black); font-weight: 800; line-height: 1; letter-spacing: -2px; white-space: nowrap;
  }
  .headline .small { font-weight: 400; letter-spacing: 0; }
  .hl-drop { left: 203px; top: 272px; font-size: 72px; }
  .hl-drop .small { font-size: 40px; }
  .hl-frock { left: 250px; top: 346px; font-size: 64px; font-style: italic; }
  .hl-days { left: 333px; top: 418px; font-size: 62px; }
  .hl-days .small { font-size: 38px; }

  .question { top: 528px; font-size: 9px; line-height: 1.3; text-align: center; }
  .question strong { display: block; color: var(--blue); font-weight: 700; font-size: 9px; text-transform: uppercase; white-space: nowrap; }
  .q-left { left: 68px; width: 240px; }
  .q-right { left: 335px; width: 225px; }

  .offer-bar {
    left: 69px; top: 593px; width: 487px; height: 30px;
    background: var(--black); color: #fff;
    font-size: 20px; line-height: 30px; padding-left: 8px; text-transform: uppercase; white-space: nowrap;
  }
  .offer-bar em { font-style: normal; font-weight: 700; color: var(--blue); }
  .get-title {
    left: 69px; top: 630px; width: 490px;
    font-size: 25px; font-weight: 700; color: var(--black); text-transform: uppercase;
    white-space: nowrap; line-height: 1.1; letter-spacing: -.4px;
  }
  .perk { top: 667px; font-size: 9px; line-height: 1.3; text-align: center; }
  .perk-1 { left: 74px; width: 152px; }
  .perk-2 { left: 233px; width: 130px; }
  .perk-3 { left: 374px; width: 90px; }
  .perk-4 { left: 472px; width: 90px; }

  .price { left: 0; width: 100%; top: 736px; text-align: center; font-size: 48px; font-weight: 300; color: var(--black); line-height: 1; white-space: nowrap; }
  .price sup { font-size: 22px; vertical-align: 20px; }
  .price strong { color: var(--blue); font-weight: 700; }
  .hurry { left: 0; width: 100%; top: 795px; text-align: center; font-size: 13px; text-transform: uppercase; white-space: nowrap; }
  .hurry strong { font-weight: 700; }
  .divider { left: 153px; top: 819px; width: 320px; height: 2px; background: var(--black); }
  .prize { left: 0; width: 100%; top: 830px; text-align: center; font-size: 17px; line-height: 1.2; text-transform: uppercase; color: var(--black); }
  .prize em { font-size: 12px; }
  .site { left: 0; width: 100%; top: 890px; text-align: center; font-size: 26px; font-weight: 400; letter-spacing: -.5px; color: var(--black); }
  .site strong { color: var(--blue); font-weight: 700; }
</style>
</head>
<body>
  <main class="poster">
    <div class="hero-photo" role="img" aria-label="Smiling woman in a turquoise tank top measuring her waist with a tape measure"></div>

    <div class="brand"><span class="brand-mark"></span>Vorelump Bootcamps</div>

    <h1 class="headline-group">
      <span class="headline hl-drop">TRIM<span class="small"> a</span></span>
      <span class="headline hl-frock">frock notch</span>
      <span class="headline hl-days"><span class="small">in </span>21 DAYS</span>
    </h1>

    <p class="question q-left"><strong>Are you tired of all the health clubs and fitness centers</strong>that tell you exactly what you want to hear to get you to join, but once you're a member they forget about you and don't teach you anything about how to get results?</p>
    <p class="question q-right"><strong>Are you frustrated</strong>by all the gimmicks; the pills, powders, shakes and gadgets sold on late night TV that are nothing more than empty promises and slick marketing?</p>

    <div class="offer-bar">If so, then this amazing offer is <em>perfect for you…</em></div>
    <h2 class="get-title">Here's what you get starting April 6th, 2015</h2>

    <p class="perk perk-1">Three weeks worth of Fat Burning Workouts with a Certified Personal Trainer to make sure that you don't spend one minute exercising that doesn't produce results.</p>
    <p class="perk perk-2">21 Days of Fat Burning Meal Plans designed by a Registered Dietician to ensure that you reach your goals as quickly as possible.</p>
    <p class="perk perk-3">Nutrition Coaching Session to answer all your questions and set you up for success</p>
    <p class="perk perk-4">21 Days of Lessons to keep you on track to achieving your goal of trimming a frock notch</p>

    <p class="price">A <sup>$</sup>327 value for <strong>ONLY <sup>$</sup>97</strong></p>
    <p class="hurry">Hurry! &nbsp;Space is limited ladies!!! &nbsp;Claim your spot now, <strong>call (555) 014-2278</strong></p>
    <div class="divider"></div>
    <p class="prize">Winner gets $100 cash, a new dress <em>(up to $100)</em><br>and a free photo shoot! <em>($150 value)</em></p>
    <p class="site"><strong>VorelumpFit</strong>.com</p>
  </main>
</body>
</html>
```